Business card design needed

I would like a one sided black business card with the information provided above. Refer to my website www.brightvolleyracquets.com.au for an example of colors I have used for my site, would like to keep this consistent for my business cards also, I will upload my logo below.

I am a new small business that provides tennis customers with racquet re stringing, tennis strings and accessories.

Industry/Entity Type

Small Business

Contact Information for Business Card

Bright Volley Tennis

Owen Whitby
Managing Director

brightvolleyracquets@mailbox.example
www.brightvolleyracquets.com.au
0491 726 305

Racquet Restringing/Tennis Strings/Accessories

Requirements
Must have
• Must have my logo and card must be black

```html
<!DOCTYPE html>
<html lang="en">
<head>
<meta charset="utf-8">
<title>Bright Volley Tennis – Business Card</title>
<link rel="stylesheet" href="https://fonts.googleapis.com/css2?family=Source+Sans+3:ital,wght@0,400;0,700;1,700&display=swap">
<style>
  :root {
    --page-bg: #e9e6e1;
    --card-black: #000000;
    --lime: #b6d433;
    --navy: #22528a;
    --white: #ffffff;
    --ink: #111111;
  }
  * { box-sizing: border-box; margin: 0; padding: 0; }
  html, body {
    width: 1200px;
    height: 750px;
    overflow: hidden;
    background: var(--page-bg);
    font-family: "Source Sans 3", "Myriad Pro", Arial, sans-serif;
  }
  .card {
    position: absolute;
    left: 75px;
    top: 75px;
    width: 1050px;
    height: 597px;
    background: var(--card-black);
    border-radius: 40px;
    overflow: hidden;
  }
  .brand {
    position: absolute;
    left: 0;
    right: 0;
    top: 150px;
    display: flex;
    justify-content: center;
    align-items: center;
    gap: 18px;
  }
  .brand-dot {
    width: 44px;
    height: 44px;
    border-radius: 50%;
    background: var(--lime);
  }
  .brand-name {
    color: var(--lime);
    font-weight: 700;
    font-size: 56px;
    letter-spacing: 1px;
    line-height: 1;
  }
  .bands {
    position: absolute;
    left: 0;
    top: 0;
    width: 1050px;
    height: 597px;
  }
  .person {
    position: absolute;
    left: 73px;
    top: 398px;
    color: var(--ink);
  }
  .person-name {
    font-weight: 700;
    font-size: 34px;
    line-height: 40px;
  }
  .person-role {
    font-size: 25px;
    line-height: 32px;
  }
  .contact {
    position: absolute;
    right: 62px;
    top: 386px;
    text-align: right;
    color: var(--white);
    font-size: 26px;
    line-height: 35px;
    list-style: none;
  }
  .contact-label {
    font-weight: 700;
    font-style: italic;
  }
  .services {
    position: absolute;
    left: 0;
    right: 0;
    top: 544px;
    display: flex;
    justify-content: center;
    gap: 16px;
    list-style: none;
    color: var(--white);
    font-size: 25px;
    line-height: 32px;
  }
  .services li::before {
    content: "";
    display: inline-block;
    width: 8px;
    height: 8px;
    background: var(--white);
    margin-right: 9px;
    vertical-align: 5px;
  }
</style>
</head>
<body>
  <div class="card">
    <div class="brand">
      <span class="brand-dot"></span>
      <span class="brand-name">Bright Volley Tennis</span>
    </div>

    <svg class="bands" viewBox="0 0 1050 597" aria-hidden="true">
      <polygon points="0,368 473,368 355,498 0,498" fill="var(--lime)"/>
      <polygon points="498,368 1050,368 1050,498 382,498" fill="var(--navy)"/>
    </svg>

    <div class="person">
      <p class="person-name">Owen Whitby</p>
      <p class="person-role">Managing Director</p>
    </div>

    <ul class="contact">
      <li><span class="contact-label">phone</span> 0491 726 305</li>
      <li><span class="contact-label">email</span> brightvolleyracquets@mailbox.example</li>
      <li><span class="contact-label">web</span> www.brightvolleyracquets.com.au</li>
    </ul>

    <ul class="services">
      <li>Racquet Restringing</li>
      <li>Tennis Strings</li>
      <li>Accessories</li>
    </ul>
  </div>
</body>
</html>
```